Lotstallmart.com Webpage Design

Design Brief for lotstallmart.com (Copy of Brief also in attached Word file)

Name of Website- lotstallmart.com (existing logo and look & feel of website to be changed)

Logo - Finalised. The logo files are attached with the brief as “logo.jpeg”. The “Blue- Grey” version of the logo is for use on lighter backgrounds and the “Orange-White” version of the logo is for use on darker backgrounds. (A full Black version of the logo is also attached). Both versions may be used in different parts of the website. All attached files are in .png format.
Status - The website in functional and is undergoing user trials. However, we want to improve the look & feel of the website so at it seems
a. cotemporary,
b. Easy to Navigate
c. professional and
d. Vibrant.

Please visit ‘lotstallmart.com’ to check out the website and its functionalities – please use it only as a reference for the features & functions to be provided, however the designer should use a ‘Free Hand’ in designing the composition of various parts of the webpage without getting too influenced by the existing design

Objective of the Website ‘lotstallmart.com –
a. It is a portal focussed on listing of ‘Retail’ specific real-estate properties by developers, owners and realty brokers. The properties shall listed under the following four categories-
i. Retail Malls
ii. Shopping Complexes
iii. High-street shops
iv. Retail Warehouses
*refer lotstallmart.com for better clarity

b. The abovementioned properties shall be listed either for ‘Sale’ or ‘rent\lease’ or both

c. Users shall visit the site in case they wish to acquire a retail \ shop space either on ‘sale’ or ‘rent’. These Users would be able to specify the ‘Search Criteria’ through the tool-bars provided on the website – the ‘Search Criteria’ shall comprise of ‘Type of space category’, ‘City’, ‘Locality’, transaction type ie ‘Rent \ Sale’ and ‘Area Range’

d. The main revenue model for the website shall be listing fee ( or advertising charges ) payable by those listing their properties on the website.

Three Main Pages of Website (lotstallmart.com) that need to be designed -
a. Main Home Page (visit the web link - http://lotstallmart.com/ ) - The main home page has the “Search Toolbar” for specifying of Search Criteria by the User. It shall also have the following features & functions-
i. Main Advertising Banner
ii. Featured Projects
iii. New Launches
iv. Toolbar with buttons – ‘Advertise with Us’, ‘Listings Alert’, ‘Mart Wizards’, ‘Advertiser Login’

b. Property Listings Page (visit the web link - http://lotstallmart.com/gurgaon-in-india ) - The List of property options that match the Criteria specified by the ‘User’ get displayed on this page.

c. Property Detail Page - When the ‘User’ clicks on the “More….” Button on the ‘Property Listings Page’ (given in point b. above) the web page with the details of the property opens. (For Example – visit the web link - http://lotstallmart.com/vorne-Shopping-Complex-vorne-quadrion-gurgaon-636 )

Note:- Please refer to attached ‘Shopping’ related images the designer may use them on the website to provide a look & feel of retail if required – either separately or rotate in a single window

Target Market(s)

Retailers & Investors looking for retail space, Real Estate Brokers, Developers

Industry/Entity Type

Advertising

Number of Pages Required

3 page

Requirements
Must have
• Refer to existing site lotstallmart.com -- all the existing functionalities are a must have.
Nice to have
• The Designer may use the retail related images on the website if required for making it more vibrant. Refer attached images Shopping(1-6).jpg

```html
<!DOCTYPE html>
<html lang="en">
<head>
<meta charset="utf-8">
<title>Lotstallmart.com – Home</title>
<link href="https://fonts.googleapis.com/css2?family=Open+Sans:wght@400;600;700&family=Noto+Serif:wght@400;700&display=swap" rel="stylesheet">
<style>
:root{
  --blue:#1e8fe6;
  --blue-dark:#1774c2;
  --ink:#2b2b2b;
  --muted:#7d7d7d;
  --light:#f0f0f0;
  --card:#efefef;
  --dark:#1d2430;
  --footer:#333333;
  --white:#ffffff;
}
*{box-sizing:border-box;margin:0;padding:0}
html,body{width:1200px;height:2711px;overflow:hidden;background:var(--white);font-family:"Open Sans",Arial,sans-serif;color:var(--ink)}
.page{position:relative;width:1200px;height:2711px}
.abs{position:absolute}

.topbar{left:0;top:0;width:1200px;height:43px;background:var(--blue)}
.topbar .promo{left:60px;top:12px;color:var(--white);font-size:13px;font-style:italic;font-weight:600}
.topbar .login{right:0;top:0;width:150px;height:43px;background:var(--blue-dark);color:var(--white);font-size:14px;display:flex;align-items:center;justify-content:center}

.header{left:0;top:43px;width:1200px;height:83px;background:var(--white)}
.brand{left:60px;top:20px;display:flex;align-items:center;gap:10px}
.brand .dot{width:36px;height:36px;border-radius:50%;background:var(--blue)}
.brand .name{font-size:32px;font-weight:700;color:var(--blue);letter-spacing:-0.5px}
.nav{right:60px;top:30px;display:flex;gap:46px;font-size:14px;color:#444}
.nav .city{color:var(--blue)}

.hero{left:0;top:126px;width:1200px;height:570px;background:radial-gradient(ellipse at 50% 40%,#6b5a48 0%,#3a2f26 45%,#1a1512 100%)}
.hero h1{left:0;width:1200px;top:500px;text-align:center;color:var(--white);font-size:29px;font-weight:600;line-height:38px;text-transform:uppercase}
.dots{left:578px;top:602px;display:flex;gap:8px}
.dots span{width:10px;height:10px;border-radius:50%;background:#8a8a8a}
.dots span.on{background:var(--blue)}

.search{left:60px;top:640px;width:1078px;height:191px;background:var(--white);box-shadow:0 2px 6px rgba(0,0,0,.3)}
.tabs{display:flex;height:44px}
.tabs div{flex:1;background:var(--blue);color:var(--white);font-size:15px;display:flex;align-items:center;justify-content:center;border-left:1px solid #5fb0ef}
.tabs div.active{background:var(--white);color:var(--blue);border-left:none}
.fields{position:absolute;left:15px;top:68px;display:flex;gap:30px}
.field{width:242px;height:40px;border:2px solid #ddd;background:#f6f6f6;font-size:12px;color:#aaa;padding:11px 12px;position:relative}
.field svg{position:absolute;right:10px;top:14px}
.btn-search{left:458px;top:128px;width:134px;height:38px;background:var(--blue);color:var(--white);font-size:17px;display:flex;align-items:center;justify-content:center}

.intro-title{left:0;width:1200px;top:868px;text-align:center;color:var(--blue);font-size:18px;font-weight:700}
.intro-sub{left:0;width:1200px;top:906px;text-align:center;color:var(--muted);font-size:14px}
.cats{left:0;width:1200px;top:946px;display:flex;justify-content:center;gap:40px;font-family:"Noto Serif",Georgia,serif;font-size:15px;color:#222}
.cats span::before{content:"";display:inline-block;width:9px;height:9px;border-radius:50%;background:var(--blue);margin-right:16px;vertical-align:1px}
.section-title{left:0;width:1200px;top:992px;text-align:center;color:var(--blue);font-size:23px;font-weight:600}

.card{width:255px;height:305px;background:var(--card);box-shadow:0 2px 3px rgba(0,0,0,.15)}
.card .img{height:181px}
.card .city{margin-top:12px;text-align:center;font-size:17px;color:#222}
.card .line{text-align:center;font-size:14px;color:var(--muted);line-height:23px}
.card .type{text-align:center;font-size:14px;color:var(--blue);line-height:23px}
.overlay{left:40px;top:70px;width:176px;height:44px;border:1px solid #ddd;color:var(--white);font-size:15px;display:flex;align-items:center;justify-content:center;gap:8px}

.launches{left:0;top:1735px;width:1200px;height:415px;background:linear-gradient(90deg,#141a24,#25303f 60%,#1a2230)}
.launches h2{left:60px;top:36px;color:var(--white);font-size:21px;font-weight:600;line-height:34px}
.citylist{left:100px;top:116px;color:#d6d6d6;font-size:15px;line-height:33px;list-style:none}
.citylist li.on{color:var(--blue);position:relative}
.citylist li.on::before{content:"";position:absolute;left:-40px;top:7px;width:4px;height:20px;background:var(--blue)}
.lcard{top:45px;width:404px;height:325px}
.lcard .img{height:186px}
.lcard .body{height:139px;padding:18px 20px;font-size:12px;line-height:20px}
.lcard .title{font-size:16px;margin-top:6px;display:flex;align-items:center;gap:8px}
.lcard .tag{color:var(--blue)}
.lcard .icons{margin-left:auto;display:flex;gap:14px}
.lcard .meta{font-size:11px;margin-top:4px}
.lcard.darkc .body{background:rgba(20,24,32,.85);color:#bbb}
.lcard.darkc .title{color:var(--white)}
.lcard.lightc .body{background:var(--white);color:#777}
.lcard.lightc .title{color:#222}

.alert{left:0;top:2150px;width:1200px;height:199px;background:#ededed}
.alert h3{left:0;width:1200px;top:30px;text-align:center;color:var(--blue);font-size:22px;font-weight:600}
.alert p{left:0;width:1200px;top:70px;text-align:center;color:#666;font-size:14px}
.ainput{top:114px;width:300px;height:44px;background:#e3e3e3;border:3px solid #d9d9d9;color:#9cc8ee;font-size:14px;padding:10px 16px}
.btn-sub{left:998px;top:114px;width:122px;height:42px;background:var(--blue);color:var(--white);font-size:18px;font-weight:600;display:flex;align-items:center;justify-content:center}

.footer{left:0;top:2349px;width:1200px;height:362px;background:var(--footer);color:#ccc}
.footer h4{font-size:22px;font-weight:400;color:var(--white)}
.footer .about{left:60px;top:32px;width:350px}
.footer .about p{font-size:11px;line-height:20px;margin-top:18px}
.fbrand{left:60px;top:180px;display:flex;align-items:center;gap:8px}
.fbrand .dot{width:28px;height:28px;border-radius:50%;background:#111}
.fbrand .name{font-size:24px;font-weight:700;color:#111}
.copy{left:60px;top:244px;font-size:11px}
.links{left:452px;top:32px}
.links .cols{display:flex;gap:80px;margin-top:18px;font-size:11px;line-height:22px}
.subs{left:808px;top:32px}
.subs .free{font-size:11px;margin-top:18px}
.sinput{width:226px;height:40px;border:2px solid #555;background:#2e2e2e;margin-top:14px;font-size:11px;padding:11px 14px}
.btn-send{width:86px;height:34px;background:#e9e9e9;color:var(--blue);font-size:17px;display:flex;align-items:center;justify-content:center;margin-top:16px}
.code{right:20px;top:10px;font-size:11px;color:#ddd}
</style>
</head>
<body>
<div class="page">

  <div class="abs topbar">
    <div class="abs promo">List Your Property Here!!</div>
    <div class="abs login">Advertiser Login</div>
  </div>

  <div class="abs header">
    <div class="abs brand"><span class="dot"></span><span class="name">lotstallmart</span></div>
    <div class="abs nav">
      <span>Home</span><span>Advertise with Us</span><span>Listings Alert</span><span>Mart Wizards</span>
      <span class="city">City ▼</span>
    </div>
  </div>

  <div class="abs hero" role="img" aria-label="Family walking with shopping bags inside a lit shopping mall"></div>
  <h1 class="abs hero-title" style="left:0;width:1200px;top:504px;text-align:center;color:#fff;font-size:29px;font-weight:600;line-height:38px">CONSECTETUR DIPING ELIT CURABITUR NON<br>GRAVIDA NISI NAM VEL MAGNA</h1>
  <div class="abs dots"><span></span><span></span><span class="on"></span></div>

  <div class="abs search">
    <div class="tabs">
      <div class="active">Retail Malls</div><div>Shopping Complex</div><div>High-street Shops</div><div>Retail Warehouse</div>
    </div>
    <div class="fields">
      <div class="field">Select Retail Format<svg width="10" height="7" viewBox="0 0 10 7"><path d="M1 1l4 4 4-4" stroke="#555" stroke-width="2" fill="none"/></svg></div>
      <div class="field">Select City:<svg width="10" height="7" viewBox="0 0 10 7"><path d="M1 1l4 4 4-4" stroke="#555" stroke-width="2" fill="none"/></svg></div>
      <div class="field">Select Locality/Micro-Market<svg width="10" height="7" viewBox="0 0 10 7"><path d="M1 1l4 4 4-4" stroke="#555" stroke-width="2" fill="none"/></svg></div>
      <div class="field">Enter Keywords:</div>
    </div>
    <div class="abs btn-search">Search</div>
  </div>

  <div class="abs intro-title">DUIS AUTEM VEL EUM IRIURE DOLOR &nbsp;IN VULPUTATE VELIT ESSE ESTIU MOLESTIE ILLUM!!</div>
  <div class="abs intro-sub">Nulla facilisi. Cras blandit elit sit amet eros sodales, non accumsan neque mollis,Nullam tempor</div>
  <div class="abs cats"><span>Retail Malls</span><span>Shopping Complex</span><span>High Street Shops</span><span>Retail Warehouses</span></div>

  <div class="abs section-title">Featured Retail Projects</div>

  <div class="abs card" style="left:60px;top:1048px">
    <div class="img" role="img" aria-label="Shopping complex building by day" style="background:linear-gradient(180deg,#9fbfd8,#b99a72 55%,#8a8a86)"></div>
    <div class="city">SURAT</div><div class="line">Velmora Arcade</div><div class="type">Shopping Complex</div>
  </div>
  <div class="abs card" style="left:336px;top:1048px">
    <div class="img" role="img" aria-label="High street tower lit at night" style="background:linear-gradient(180deg,#2f4a7a,#6b5a44 60%,#1f1e24)"></div>
    <div class="city">FARIDABAD</div><div class="line">Kestrel 81 High Street</div><div class="line">Sector-81</div><div class="type">Shopping Complex</div>
  </div>
  <div class="abs card" style="left:611px;top:1048px">
    <div class="img" role="img" aria-label="Mall facade glowing at dusk" style="background:linear-gradient(180deg,#3a3d48,#b36a3e 55%,#2a2420)"></div>
    <div class="city">NEW DELHI</div><div class="line">Harbourline Mall-Tagore Garden</div><div class="line">Tagore Garden</div><div class="type">Shopping Complex</div>
  </div>
  <div class="abs card" style="left:885px;top:1048px">
    <div class="img" role="img" aria-label="Mall exterior under dark overlay" style="background:linear-gradient(180deg,#2a2c31,#3a3b40)"></div>
    <div class="abs overlay"><svg width="14" height="14" viewBox="0 0 14 14"><path d="M6 8l2-2M5 6L3 8a2 2 0 003 3l2-2M9 8l2-2a2 2 0 00-3-3L6 5" stroke="#fff" stroke-width="1.5" fill="none"/></svg>View The Listing</div>
    <div class="city">CHENNAI</div><div class="line">Solvane Skyway Mall</div><div class="line">Aminjikarai</div><div class="type">Shopping Complex</div>
  </div>

  <div class="abs card" style="left:60px;top:1390px">
    <div class="img" role="img" aria-label="Mall building lit at night" style="background:linear-gradient(180deg,#1a1a22,#9a5a28 60%,#2a1a14)"></div>
    <div class="city">CHENNAI</div><div class="line">The Meridian Mall</div><div class="line">Velacheri</div><div class="type">Retail Malls</div>
  </div>
  <div class="abs card" style="left:336px;top:1390px">
    <div class="img" role="img" aria-label="High street tower lit at night" style="background:linear-gradient(180deg,#2f4a7a,#6b5a44 60%,#1f1e24)"></div>
    <div class="city">FARIDABAD</div><div class="line">Kestrel 81 High Street</div><div class="line">Sector-81</div><div class="type">Shopping Complex</div>
  </div>
  <div class="abs card" style="left:611px;top:1390px">
    <div class="img" role="img" aria-label="Mall facade glowing at dusk" style="background:linear-gradient(180deg,#3a3d48,#b36a3e 55%,#2a2420)"></div>
    <div class="city">NEW DELHI</div><div class="line">Harbourline Mall-Tagore Garden</div><div class="line">Tagore Garden</div><div class="type">Shopping Complex</div>
  </div>
  <div class="abs card" style="left:885px;top:1390px">
    <div class="img" role="img" aria-label="Mall exterior against blue sky" style="background:linear-gradient(180deg,#6f9ed6,#b27a62 55%,#7b6c66)"></div>
    <div class="city">CHENNAI</div><div class="line">Solvane Skyway Mall</div><div class="line">Aminjikarai</div><div class="type">Shopping Complex</div>
  </div>

  <div class="abs launches" role="img" aria-label="Dark backdrop of city towers">
    <h2 class="abs">Featured<br>New Launches</h2>
    <ul class="abs citylist">
      <li>Chennai</li><li>Gurgaon</li><li>New Delhi</li><li class="on">BANGLORE</li><li>Bhopal</li><li>Mysore</li><li>Thiruvananthapuram</li><li>Faridabad</li>
    </ul>

    <div class="abs lcard darkc" style="left:329px">
      <div class="img" role="img" aria-label="Glass commercial tower at twilight" style="background:linear-gradient(180deg,#2e5a9c,#5c6f98 60%,#2a2e3a)"></div>
      <div class="body">
        Fusce sollicitudin porttitor sapien, eu gravida urna ultricies nec.<br>Suspendisse volutpat nisl eget sem pretium.
        <div class="title">NOIDA, <span style="font-size:14px">Crestline One Sector-18</span> <span class="tag">Retail Malls</span>
          <span class="icons"><svg width="14" height="14" viewBox="0 0 14 14"><path d="M2 12l10-10M8 2h4v4M6 12H2V8" stroke="currentColor" stroke-width="1.5" fill="none"/></svg><svg width="14" height="13" viewBox="0 0 14 13"><path d="M7 12L1.5 6.5a3 3 0 015-4L7 3l.5-.5a3 3 0 015 4z" stroke="currentColor" stroke-width="1.4" fill="none"/></svg></span></div>
        <div class="meta">⌂ Building Area</div>
      </div>
    </div>

    <div class="abs lcard lightc" style="left:734px">
      <div class="img" role="img" aria-label="Mall tower with blue tint" style="background:linear-gradient(180deg,#3f86d8,#2f6cc0)">
        <svg class="abs" style="left:174px;top:74px" width="56" height="42" viewBox="0 0 56 42"><rect x="1" y="1" width="54" height="40" fill="none" stroke="#fff" stroke-width="1.5"/><path d="M16 21c4-6 20-6 24 0-4 6-20 6-24 0z" fill="#fff"/><circle cx="28" cy="21" r="3" fill="#3f86d8"/></svg>
      </div>
      <div class="body">
        Fusce sollicitudin porttitor sapien, eu gravida urna ultricies nec.<br>Suspendisse volutpat nisl eget sem pretium.
        <div class="title">BANGALORE, <span style="font-size:14px">Nimbus Mall</span> <span class="tag">Retail Malls</span>
          <span class="icons"><svg width="14" height="14" viewBox="0 0 14 14"><path d="M2 12l10-10M8 2h4v4M6 12H2V8" stroke="currentColor" stroke-width="1.5" fill="none"/></svg><svg width="14" height="13" viewBox="0 0 14 13"><path d="M7 12L1.5 6.5a3 3 0 015-4L7 3l.5-.5a3 3 0 015 4z" stroke="currentColor" stroke-width="1.4" fill="none"/></svg></span></div>
        <div class="meta">⌂ Building Area</div>
      </div>
    </div>
  </div>

  <div class="abs alert">
    <h3 class="abs">Listing Alert</h3>
    <p class="abs">Suscribe &nbsp;for Fortnightly Email update on New Listings @ Lotstallmart</p>
    <div class="abs ainput" style="left:78px">Enter Email Address</div>
    <div class="abs ainput" style="left:408px">Select Option</div>
    <div class="abs ainput" style="left:704px">Select cities of interest</div>
    <div class="abs btn-sub">Subscribe</div>
  </div>

  <div class="abs footer">
    <div class="abs code">C13</div>
    <div class="abs about">
      <h4>About Us</h4>
      <p>Lotstallmart.com is a Specialised Web based platform for Retail Space, featuring properties across India under various formats such as Retail Malls, Shopping Complexes, High-street Shops.....</p>
    </div>
    <div class="abs fbrand"><span class="dot"></span><span class="name">lotstallmart</span></div>
    <div class="abs copy">Copyright © 2013 Retail Grid Central.com. All rights reserved.</div>
    <div class="abs links">
      <h4>Quick Links</h4>
      <div class="cols">
        <div>About Us<br>Privacy Policy<br>Terms of Use<br>Contact Us<br>Site Map</div>
        <div>Retail Malls<br>Shopping Complex<br>High Street Shops<br>Retail Warehouses</div>
      </div>
    </div>
    <div class="abs subs">
      <h4>Quick Links</h4>
      <div class="free">This is a Free Service!</div>
      <div class="sinput">Email</div>
      <div class="sinput">Mobile</div>
      <div class="sinput" style="height:66px">Add Subscription of Requirements</div>
      <div class="btn-send">Send</div>
    </div>
  </div>

</div>
</body>
</html>
```